Hello Creative Minds!
Our business is after a elegant and classy flyer that draws attention!
The business is Velvet Turf - Lawn Revival Services. We provide services that maintain a healthy and vibrant green lawn through the tough Australian seasons. The products we use limits the water needed to keep grass green to a minimum - practically none at all! This not only helps the home owner or home seller but the environment by limiting the use of water that is needed to create a green lawn. The products we use are made from natural ingredients that are and pet friendly.
This fly will be our introductory offer to the market. Below are the required points that need to be on the flyer. Attached is the business logo, before & after pictures and 1 example of the LAYOUT not DESIGN of what the flyer should be laid out like or similar to. Feel free to use different 'Lawn Mower' pictures.
All the best; if you need any questions answered please feel free to message.
REQUIRED POINTS (Please re-phrase were possible);
*Instantly restores the natural green colour of grass – year round
*Lasts for up to 3 months
*Substantially reduces watering needs
*Pet friendly
*Stays green during droughts and water restrictions
*UV fade resistant
*Won’t bleed, run, or stain once absorbed into the grass
*Safe for the environment, pets and people
*Works in extreme heat, cold and frost
*Organic and natural – no harmful chemicals
*Reduces the amount of fertilizer
and water used on lawns
*Kerb appeal is essential for getting your property sold for the highest price possible
SERVICES & PRICING
Lawn maintenance (cut & trim) starting from $60
Lawn rejuvenation starting from $80 (Only $27 a month for 3 months)*
Package deal starting from $120
Introductory offer: 25% off all services. Refer a friend, when they book you receive another 25% off your next service.
LOCATIONS
Nowra to Sydney
CONTACT NUMBER
Will be posted with the winner - please leave an area for this.
SOCIAL MEDIA
Please add Chatterbook and Snapgrid logo's
Updates
Target Market(s)
home owners, home sellers, property developers, real estates and nursing homes and government housing.
Industry/Entity Type
Lawn Care
Look and feel
Each slider illustrates characteristics of the customer's brand and the style your logo design should communicate.

```html
<!DOCTYPE html>
<html lang="en">
<head>
<meta charset="utf-8">
<title>Velvet Turf - Lawn Revival Services Flyer</title>
<link rel="stylesheet" href="https://fonts.googleapis.com/css2?family=Montserrat:wght@400;500;600;700&display=swap">
<style>
:root{
  --bg:#dcdcdc;
  --green:#2f7a22;
  --green-dark:#24641a;
  --lime:#8dc63f;
  --lime-soft:#a9d468;
  --yellow:#f4e600;
  --white:#ffffff;
  --ink:#1b1b1b;
  --sky:#8fb6dc;
  --leaf:#4f8a2e;
}
*{margin:0;padding:0;box-sizing:border-box}
html,body{width:1200px;height:900px;overflow:hidden;background:var(--bg)}
body{font-family:"Montserrat",Arial,sans-serif;position:relative}
.flyer{position:absolute;left:265px;top:20px;width:670px;height:860px;background:var(--green);overflow:hidden;box-shadow:0 6px 18px rgba(0,0,0,.25)}
.hero-photo{position:absolute;left:0;top:0;width:670px;height:420px;background:linear-gradient(180deg,var(--sky) 0%,#c9dcec 22%,#6f9a4a 55%,var(--leaf) 100%)}
.swoosh{position:absolute;left:0;top:300px;width:670px;height:140px}
.brand{position:absolute;left:60px;top:282px;color:var(--white)}
.brand-name{font-size:40px;font-weight:600;letter-spacing:1px;line-height:1}
.brand-tag{font-size:11px;font-weight:500;letter-spacing:5px;margin-top:8px;padding-left:34px;line-height:1.2}
.result-circle{position:absolute;left:490px;top:252px;width:158px;height:158px;border-radius:50%;border:5px solid var(--yellow);background:linear-gradient(90deg,#c9a86a 0%,#b89455 50%,#5b9a33 50%,#3f7f25 100%)}
.result-label{position:absolute;font-size:11px;color:var(--white)}
.result-label.before{left:14px;top:44px}
.result-label.after{right:16px;bottom:34px}
.price-band{position:absolute;left:0;top:458px;width:670px;height:70px;background:var(--lime-soft)}
.price-band::after{content:"";position:absolute;left:0;right:0;top:34px;border-top:2px dashed var(--white)}
.offers{position:absolute;left:38px;top:432px;display:flex;gap:16px}
.offer{width:137px;text-align:center}
.offer-title{font-size:12px;color:var(--yellow);margin-bottom:6px;height:14px}
.coupon{position:relative;background:var(--white);height:80px;padding:5px}
.coupon-inner{border:1.5px dashed var(--green);height:100%;display:flex;flex-direction:column;align-items:center;justify-content:center;color:var(--ink)}
.coupon-from{font-size:8px}
.coupon-price{font-size:38px;font-weight:600;letter-spacing:-1.5px;line-height:1}
.coupon-star{font-size:10px;vertical-align:top}
.coupon-note{font-size:6.5px}
.coupon-deal{font-size:27px;font-weight:700;letter-spacing:-1px;line-height:1}
.coupon-sub{font-size:7px}
.coupon-fine{font-size:5.5px;color:var(--green);line-height:1.25;margin-top:3px;padding:0 4px}
.headline{position:absolute;left:62px;top:552px;font-size:17.5px;color:var(--yellow);font-weight:500;letter-spacing:-.2px}
.benefits{position:absolute;top:584px;list-style:none;color:var(--white);font-size:12.5px;line-height:1.2;width:270px}
.benefits.left{left:66px}
.benefits.right{left:348px}
.benefits li{margin-bottom:5px;position:relative;padding-left:10px}
.benefits li::before{content:"";position:absolute;left:0;top:5px;width:6px;height:6px;border-radius:50%;background:var(--yellow)}
.footer{position:absolute;left:0;top:806px;width:670px;height:54px;background:var(--white)}
.contact-pill{position:absolute;left:112px;top:790px;width:445px;height:28px;border-radius:14px;background:var(--lime);display:flex;align-items:center;justify-content:center;gap:28px;color:var(--white);font-size:14px;font-weight:500}
.contact-item{display:flex;align-items:center;gap:6px}
.socials{position:absolute;left:0;top:826px;width:670px;display:flex;justify-content:center;gap:26px;font-size:13px;color:var(--ink)}
.social{display:flex;align-items:center;gap:6px}
.social-mark{width:11px;height:11px;background:var(--green)}
</style>
</head>
<body>
<main class="flyer">
  <div class="hero-photo" role="img" aria-label="Low-angle photograph of a lawn mower on fresh green grass under trees and blue sky"></div>
  <svg class="swoosh" viewBox="0 0 670 140" aria-hidden="true">
    <path d="M0 140 L0 70 Q260 130 670 40 L670 140 Z" fill="var(--green)"/>
    <path d="M0 58 Q260 120 670 28" fill="none" stroke="var(--white)" stroke-width="5"/>
    <path d="M0 66 Q260 128 670 36" fill="none" stroke="var(--yellow)" stroke-width="5"/>
  </svg>
  <div class="brand">
    <div class="brand-name">Velvet Turf</div>
    <div class="brand-tag">LAWN REVIVAL SERVICES</div>
  </div>
  <div class="result-circle" role="img" aria-label="Before and after photo of a lawn, dry straw on the left and green grass on the right">
    <span class="result-label before">Before</span>
    <span class="result-label after">After</span>
  </div>

  <div class="price-band"></div>
  <section class="offers">
    <div class="offer">
      <div class="offer-title">Lawn Maintenance</div>
      <div class="coupon"><div class="coupon-inner"><span class="coupon-from">starting from</span><span class="coupon-price">60$</span></div></div>
    </div>
    <div class="offer">
      <div class="offer-title">Lawn Rejuvenation</div>
      <div class="coupon"><div class="coupon-inner"><span class="coupon-from">starting from</span><span class="coupon-price">80$<span class="coupon-star">*</span></span><span class="coupon-note">*only 27$ a month for 3 months</span></div></div>
    </div>
    <div class="offer">
      <div class="offer-title">Package Deal</div>
      <div class="coupon"><div class="coupon-inner"><span class="coupon-from">starting from</span><span class="coupon-price">120$</span></div></div>
    </div>
    <div class="offer">
      <div class="offer-title">Introductory Offer</div>
      <div class="coupon"><div class="coupon-inner"><span class="coupon-deal">25% OFF</span><span class="coupon-sub">for all services</span><span class="coupon-fine">Refer a friend. When they book you receive another 25% off your next service.</span></div></div>
    </div>
  </section>

  <h2 class="headline">Instantly restores the natural green colour of grass – year round!</h2>
  <ul class="benefits left">
    <li>Lasts for up to 3 months</li>
    <li>Substantially reduces watering needs</li>
    <li>Pet friendly</li>
    <li>Stays green during droughts and water restrictions</li>
    <li>UV fade resistant</li>
    <li>Won’t bleed, run, or stain once absorbed into the grass</li>
  </ul>
  <ul class="benefits right">
    <li>Safe for the environment, pets and people</li>
    <li>Works in extreme heat, cold and frost</li>
    <li>Organic and natural – no harmful chemicals</li>
    <li>Reduces the amount of fertilizer and water used on lawns</li>
    <li>Kerb appeal is essential for getting your property sold for the highest price</li>
  </ul>

  <div class="footer"></div>
  <div class="contact-pill">
    <span class="contact-item">
      <svg width="16" height="16" viewBox="0 0 16 16" aria-hidden="true"><circle cx="8" cy="8" r="7" fill="none" stroke="var(--white)" stroke-width="1.5"/><path d="M5.5 4.5l1.5 0 .6 1.8-1 .8a5 5 0 002.3 2.3l.8-1 1.8.6v1.5c-3.5.3-6.3-2.5-6-6z" fill="var(--white)"/></svg>
      Telephone
    </span>
    <span class="contact-item">
      <svg width="11" height="15" viewBox="0 0 11 15" aria-hidden="true"><path d="M5.5 0A5.5 5.5 0 000 5.5C0 9.5 5.5 15 5.5 15S11 9.5 11 5.5A5.5 5.5 0 005.5 0zm0 7.7a2.2 2.2 0 110-4.4 2.2 2.2 0 010 4.4z" fill="var(--white)"/></svg>
      Locations from Nowra to Sydney
    </span>
  </div>
  <div class="socials">
    <span class="social"><span class="social-mark"></span>velvetturf</span>
    <span class="social"><span class="social-mark"></span>chatterbook.com/velvetturf</span>
  </div>
</main>
</body>
</html>
```